Awesome photographers card for an awesome new business

Double sided business card Black background and silver logo in middle on one side. Details on otherside. please keep it simple

Industry/Entity Type

Photographer

Contact Information for Business Card

Gerald Fenwick
0452817360
GeraldFenwickPhotography47@mailbox.test
www.GeraldFenwickPhotography.test.au
Instagram _Gerald_fenwick

Requirements
Must have
• My logo in Silver
• please use instagram logo instead of "Instagram"

```html
<!DOCTYPE html>
<html lang="en">
<head>
<meta charset="utf-8">
<title>Gerald Fenwick Photography – Business Card</title>
<link rel="stylesheet" href="https://fonts.googleapis.com/css2?family=Roboto:wght@400;700&family=Roboto+Condensed:wght@700&family=Questrial&display=swap">
<style>
  :root {
    --backdrop: #d2a77f;
    --card-front: #f7f7f6;
    --card-back: #1d1f21;
    --silver: #8e8e8e;
    --silver-light: #b5b5b5;
    --ink-grey: #4a4a4a;
    --detail-text: #e4e4e4;
  }
  * { box-sizing: border-box; margin: 0; padding: 0; }
  html, body { width: 1200px; height: 960px; overflow: hidden; }
  body { background: var(--backdrop); position: relative; }

  .card {
    position: absolute;
    left: 320px;
    width: 600px;
    height: 343px;
    border-radius: 22px;
  }
  .card--front { top: 102px; background: var(--card-front); }
  .card--back  { top: 493px; background: var(--card-back); }

  .brand-mark {
    position: absolute;
    left: 212px;
    top: 80px;
    width: 176px;
    height: 176px;
    border: 3px solid var(--silver);
    border-radius: 50%;
    display: flex;
    flex-direction: column;
    align-items: center;
    justify-content: center;
    font-family: "Roboto", sans-serif;
    font-weight: 400;
    color: var(--silver);
    text-align: center;
  }
  .brand-mark__name { font-size: 19px; line-height: 1.25; }
  .brand-mark__trade { font-size: 11px; letter-spacing: 3px; text-transform: uppercase; margin-top: 4px; }

  .front-web {
    position: absolute;
    left: 0; right: 0;
    top: 298px;
    text-align: center;
    font-family: "Roboto", sans-serif;
    font-size: 15px;
    letter-spacing: 2.2px;
    color: var(--ink-grey);
  }

  .holder-name {
    position: absolute;
    right: 36px;
    top: 190px;
    font-family: "Roboto Condensed", sans-serif;
    font-weight: 700;
    font-size: 21px;
    color: var(--silver-light);
    text-transform: uppercase;
  }
  .contact-list {
    position: absolute;
    right: 38px;
    top: 232px;
    list-style: none;
    font-family: "Questrial", sans-serif;
    font-size: 15px;
    color: var(--detail-text);
  }
  .contact-list li {
    display: flex;
    justify-content: flex-end;
    align-items: center;
    gap: 12px;
    height: 19.5px;
  }
  .contact-icon { width: 13px; height: 13px; flex: none; }
</style>
</head>
<body>
  <section class="card card--front" aria-label="Card front">
    <div class="brand-mark">
      <span class="brand-mark__name">Gerald Fenwick</span>
      <span class="brand-mark__trade">Photography</span>
    </div>
    <p class="front-web">www.GeraldFenwickPhotography.test.au</p>
  </section>

  <section class="card card--back" aria-label="Card back">
    <h1 class="holder-name">Gerald Fenwick</h1>
    <ul class="contact-list">
      <li>0452817360
        <svg class="contact-icon" viewBox="0 0 16 16" aria-hidden="true"><path fill="#a5a5a5" d="M3.5 1l2.5 3-1.5 1.6c.8 2 2.4 3.6 4.4 4.4L10.5 8.5l3 2.5-1.6 2.8C6.5 13.5 2.5 9.5 1 4z"/></svg>
      </li>
      <li>GeraldFenwickPhotography47@mailbox.test
        <svg class="contact-icon" viewBox="0 0 16 16" aria-hidden="true"><rect x="1" y="3" width="14" height="10" fill="#a5a5a5"/><path d="M1 3l7 6 7-6" fill="none" stroke="#1d1f21" stroke-width="1.4"/></svg>
      </li>
      <li>www.GeraldFenwickPhotography.test.au
        <svg class="contact-icon" viewBox="0 0 16 16" aria-hidden="true"><circle cx="8" cy="8" r="7" fill="#a5a5a5"/><path d="M1 8h14M8 1c-3 3.5-3 10.5 0 14M8 1c3 3.5 3 10.5 0 14" fill="none" stroke="#1d1f21" stroke-width="1.1"/></svg>
      </li>
      <li>Gerald_fenwick
        <svg class="contact-icon" viewBox="0 0 16 16" aria-hidden="true"><rect x="1" y="1" width="14" height="14" rx="2" fill="#a5a5a5"/></svg>
      </li>
    </ul>
  </section>
</body>
</html>
```